Business Card Design

Electronic Security Installation Specialists

Check out our website at www.tallbrookllc.com to see what we do.

Industry/Entity Type

Business

Contact Information for Business Card

Tall Brook
Marjorie Hadley
281 Orchard Rise
Mapleton, WV 25871

Colors
3176b5
0455a3
ffffff

```html
<!DOCTYPE html>
<html lang="en">
<head>
<meta charset="utf-8">
<title>Tall Brook — Business Card</title>
<link rel="stylesheet" href="https://fonts.googleapis.com/css2?family=Open+Sans:wght@400;600;700&display=swap">
<style>
  :root {
    --brand-blue: #3176b5;
    --brand-navy: #0455a3;
    --paper: #ffffff;
    --ink: #2b2b2b;
    --stage: #eceae6;
    --faint: #eef0f2;
    --card-w: 540px;
    --card-h: 309px;
  }
  * { box-sizing: border-box; margin: 0; padding: 0; }
  html, body {
    width: 1200px; height: 913px; overflow: hidden;
    background: var(--stage);
    font-family: "Open Sans", Arial, sans-serif;
  }
  .stage {
    width: 1200px; height: 913px;
    display: flex; align-items: center; justify-content: center; gap: 50px;
  }
  .card {
    position: relative;
    width: var(--card-w); height: var(--card-h);
    background: var(--paper);
    box-shadow: 0 6px 18px rgba(0,0,0,0.14);
    overflow: hidden;
  }
  .card__decor {
    position: absolute;
    left: 40px; right: 40px; top: 30px; bottom: 30px;
    border-radius: 50%;
    background: radial-gradient(ellipse at center, transparent 58%, var(--faint) 60%, var(--faint) 64%, transparent 66%);
  }
  .brand {
    position: absolute;
    display: flex; align-items: center; gap: 12px;
    color: var(--brand-blue);
    font-weight: 700;
    white-space: nowrap;
  }
  .brand__dot {
    border-radius: 50%;
    background: var(--brand-navy);
    flex: none;
  }
  .card--front .brand {
    left: 50%; top: 50%; transform: translate(-50%, -50%);
    font-size: 40px;
  }
  .card--front .brand__dot { width: 44px; height: 44px; }
  .card--back .brand {
    right: 28px; top: 28px;
    font-size: 24px;
  }
  .card--back .brand__dot { width: 26px; height: 26px; }
  .contact {
    position: absolute; left: 40px; top: 112px;
    color: var(--ink);
  }
  .contact__name {
    color: var(--brand-blue);
    font-size: 19px; font-weight: 700; line-height: 1.1;
  }
  .contact__title {
    font-size: 12.5px; margin: 2px 0 0 14px;
  }
  .contact__address {
    font-size: 12.5px; line-height: 1.35; margin: 40px 0 4px 0;
    font-style: normal;
  }
  .contact__list { list-style: none; font-size: 12.5px; line-height: 1.4; }
  .contact__list li { display: flex; align-items: center; gap: 8px; }
  .contact__list svg { width: 11px; height: 11px; fill: var(--brand-navy); flex: none; }
  .contact__web { color: var(--brand-navy); font-weight: 600; }
  .card__band {
    position: absolute; left: 0; bottom: 0; width: 100%; height: 40px;
  }
</style>
</head>
<body>
<main class="stage">
  <section class="card card--front" aria-label="Card front">
    <div class="card__decor" role="img" aria-label="Faint brand decoration"></div>
    <div class="brand"><span class="brand__dot"></span>Tall Brook</div>
  </section>

  <section class="card card--back" aria-label="Card back">
    <div class="card__decor" role="img" aria-label="Faint brand decoration"></div>
    <div class="brand"><span class="brand__dot"></span>Tall Brook</div>

    <div class="contact">
      <p class="contact__name">Marjorie Hadley</p>
      <p class="contact__title">Managing Director</p>
      <address class="contact__address">281 Orchard Rise<br>Mapleton, WV 25871</address>
      <ul class="contact__list">
        <li><svg viewBox="0 0 12 12"><path d="M2.5 1 4.5 1 5.3 3.4 4 4.3a6 6 0 0 0 3.7 3.7L8.6 6.7 11 7.5v2a1.3 1.3 0 0 1-1.4 1.3A9.5 9.5 0 0 1 1.2 2.4 1.3 1.3 0 0 1 2.5 1Z"/></svg>304-555-0187</li>
        <li><svg viewBox="0 0 12 12"><path d="M1 3h10v6H1Zm.8.6L6 6.6l4.2-3Z"/></svg>m.hadley@tallbrookllc.com</li>
        <li><svg viewBox="0 0 12 12"><circle cx="6" cy="6" r="5"/></svg><span class="contact__web">www.tallbrookllc.com</span></li>
      </ul>
    </div>

    <svg class="card__band" viewBox="0 0 540 40" preserveAspectRatio="none" aria-hidden="true">
      <polygon points="0,22 300,22 318,4 540,4 540,40 0,40" fill="var(--brand-blue)"/>
      <polygon points="0,30 300,30 318,14 540,14 540,40 0,40" fill="var(--brand-navy)"/>
    </svg>
  </section>
</main>
</body>
</html>
```